Restaurant Facility Equipment & Store Maintenance/

I need a flyer showing commercial/industrial kitchen equipment photos we work on Hot Equipment & Cold Equipment and offer many services. see attached highlights

```html
<!DOCTYPE html>
<html lang="en">
<head>
<meta charset="utf-8">
<title>Restaurant Facility Equipment &amp; Store Maintenance</title>
<link href="https://fonts.googleapis.com/css2?family=Kanit:wght@600;700&family=Poppins:wght@400;500;600;700;800&display=swap" rel="stylesheet">
<style>
  :root{
    --navy:#0b1f45;
    --navy-deep:#07162f;
    --blue:#0f3b80;
    --blue-bright:#1c56b0;
    --yellow:#ffd400;
    --yellow-deep:#ffc107;
    --red:#e8141b;
    --ink:#0f1a2c;
    --white:#ffffff;
    --page:#ececec;
  }
  *{box-sizing:border-box;margin:0;padding:0}
  html,body{width:1007px;height:1200px;overflow:hidden;background:var(--page)}
  body{font-family:"Poppins",sans-serif;position:relative}
  .flyer{position:absolute;left:39px;top:0;width:928px;height:1200px;overflow:hidden;background:var(--white)}
  .abs{position:absolute}

  /* hero */
  .hero{left:0;top:0;width:928px;height:404px;
    background:radial-gradient(ellipse at 75% 60%,#1d4f9c 0%,#123a7a 40%,transparent 75%),
               linear-gradient(100deg,#081a3a 0%,#0c2753 45%,#15438a 100%)}
  .title{left:0;top:50px;width:928px;text-align:center;font-family:"Kanit",sans-serif;font-weight:700;
    font-size:52px;line-height:48px;letter-spacing:-0.3px;text-transform:uppercase}
  .title .white{color:var(--white)}
  .title .yellow{color:var(--yellow)}
  .tagline{left:0;top:207px;width:928px;text-align:center;color:var(--white);font-weight:600;font-size:14.5px;letter-spacing:5.6px}
  .area-pill{left:310px;top:240px;width:312px;height:37px;border-radius:0 19px 19px 0;border:1.5px solid var(--yellow);border-left:none;
    display:flex;align-items:center;padding-left:24px;gap:8px;color:var(--white);font-weight:500;font-size:14.5px}

  /* yellow band */
  .band{left:0;top:404px;width:928px;height:194px;background:linear-gradient(90deg,var(--yellow) 0%,#ffdb00 60%,var(--yellow-deep) 100%)}
  .tile{width:138px;height:138px;transform:rotate(45deg);border:3px solid var(--yellow);border-radius:14px;overflow:hidden;
    box-shadow:0 10px 14px rgba(0,0,0,.18)}
  .tile-fill{width:100%;height:100%}
  .handle{left:0;top:527px;width:928px;text-align:center;font-weight:700;font-size:19.5px;color:var(--ink);letter-spacing:-0.2px}
  .handle-sub{left:0;top:557px;width:928px;text-align:center;font-size:15px;color:var(--ink)}

  /* equipment services */
  .eq-title{left:60px;top:620px;color:var(--blue);font-weight:700;font-size:17px}
  .eq-item{left:62px;display:flex;align-items:center;gap:11px;font-size:13.5px;color:var(--ink)}
  .eq-icon{width:38px;height:38px;border-radius:50%;background:var(--navy);border:2.5px solid var(--yellow);display:flex;align-items:center;justify-content:center}
  .badge{height:35px;border-radius:4px}
  .badge-a{left:62px;top:876px;width:104px;background:var(--white);border:3px solid #a31419}
  .badge-b{left:186px;top:878px;width:95px;height:31px;background:#1a2a44;border-radius:16px}

  /* why choose */
  .why{left:431px;top:598px;width:410px;height:229px;background:var(--navy);border-radius:0 0 16px 16px;overflow:hidden}
  .why-strip{left:0;top:0;width:34px;height:229px;background:linear-gradient(180deg,#8a8a25 0%,#3b4a3a 25%,var(--navy) 55%)}
  .why-label{left:18px;top:212px;transform:rotate(-90deg);transform-origin:0 0;color:var(--white);font-weight:800;font-size:14px;letter-spacing:2.6px;white-space:nowrap;margin-left:-8px}
  .why-list{left:54px;top:28px;width:348px;list-style:none}
  .why-list li{display:flex;gap:7px;color:var(--white);font-size:12.5px;line-height:14.5px;margin-bottom:14.5px}
  .tick{flex:none;width:12px;height:12px;margin-top:1px}

  /* emergency */
  .emergency{left:429px;top:844px;color:var(--red);font-weight:800;font-size:30px;line-height:32px;letter-spacing:-0.4px}
  .repairs{left:429px;top:873px;color:var(--ink);font-weight:800;font-size:42px;line-height:44px;letter-spacing:-0.5px}
  .avail{left:637px;top:897px;width:117px;height:17px;background:var(--red);border-radius:4px;color:var(--white);font-weight:700;font-size:10.5px;letter-spacing:2px;text-align:center;line-height:17px}

  /* footer */
  .footer{left:0;top:940px;width:928px;height:260px;background:linear-gradient(90deg,var(--blue) 0%,var(--navy) 40%,var(--navy-deep) 100%)}
  .tab{left:344px;top:940px;width:247px;height:33px}
  .tab-text{left:344px;top:945px;width:247px;text-align:center;color:var(--navy);font-weight:700;font-size:16px}
  .support{list-style:none}
  .support li{display:flex;align-items:center;gap:4px;color:var(--white);font-size:12.5px;line-height:18.3px}
  .support-left{left:66px;top:988px}
  .support-right{left:445px;top:990px}
  .divider{left:427px;top:992px;height:64px;border-left:1.5px dashed rgba(255,255,255,.6)}
  .worker{left:722px;top:1040px;width:206px;height:160px;border-radius:90px 90px 0 0;background:linear-gradient(180deg,#3b6fc0 0%,#1f4ea0 60%,#173c80 100%)}
  .cta{left:60px;top:1089px;width:319px;height:32px;background:var(--yellow);border-radius:16px 0 0 16px;color:var(--navy);font-weight:700;font-size:13.8px;line-height:32px;padding-left:22px}
  .cta-note{left:379px;top:1089px;width:431px;height:32px;background:var(--blue-bright);color:var(--white);font-weight:700;font-size:13.8px;line-height:32px;padding-left:10px;letter-spacing:-0.2px}
  .contacts{left:66px;top:1131px;display:flex;align-items:center;color:var(--white);font-size:15px;letter-spacing:1px}
  .contacts .sep{margin:0 20px 0 26px;opacity:.9}
  .contacts .item{display:flex;align-items:center;gap:9px}
</style>
</head>
<body>
<div class="flyer">

  <div class="abs hero" role="img" aria-label="Commercial kitchen interior photo in blue tones"></div>

  <h1 class="abs title">
    <span class="white">Restaurant Facility</span><br>
    <span class="yellow">Equipment &amp;</span><br>
    <span class="yellow">Store Maintenance</span>
  </h1>
  <p class="abs tagline">COMMERCIAL &amp; INDUSTRIAL KITCHEN SERVICES</p>
  <div class="abs area-pill">
    <svg width="16" height="20" viewBox="0 0 16 20"><path d="M8 1a6 6 0 0 0-6 6c0 4.5 6 11 6 11s6-6.5 6-11a6 6 0 0 0-6-6z" fill="#e8141b"/><circle cx="8" cy="7" r="2.3" fill="#fff"/></svg>
    Denver Metro &amp; Surrounding Areas
  </div>

  <div class="abs band"></div>

  <div class="abs tile" style="left:98px;top:328px"><div class="tile-fill" role="img" aria-label="Stainless steel commercial kitchen line" style="background:linear-gradient(135deg,#c9d0d8,#6d7784)"></div></div>
  <div class="abs tile" style="left:296px;top:328px"><div class="tile-fill" role="img" aria-label="Technician repairing plumbing under a kitchen sink" style="background:linear-gradient(135deg,#b9b3aa,#55606b)"></div></div>
  <div class="abs tile" style="left:493px;top:328px"><div class="tile-fill" role="img" aria-label="Worker in yellow apron cleaning kitchen equipment" style="background:linear-gradient(135deg,#e1d3a2,#6a6050)"></div></div>
  <div class="abs tile" style="left:691px;top:328px"><div class="tile-fill" role="img" aria-label="Technician servicing a kitchen exhaust hood" style="background:linear-gradient(135deg,#c8ccd2,#5d6a80)"></div></div>

  <p class="abs handle">WE HANDLE EVERYTHING FROM THE FRONT DOOR TO THE BACK DOOR</p>
  <p class="abs handle-sub">Installation, Rebuilds, OSHA Inspection, and Preventive Maintenance Services.</p>

  <h2 class="abs eq-title">Hot &amp; &nbsp;Cold Equipment Services</h2>
  <div class="abs eq-item" style="top:651px"><span class="eq-icon"><svg width="18" height="18" viewBox="0 0 18 18"><circle cx="9" cy="9" r="6" fill="none" stroke="#fff" stroke-width="3" stroke-dasharray="3 1.7"/><circle cx="9" cy="9" r="2.2" fill="#fff"/></svg></span>Installation, Repair &amp; Rebuilds</div>
  <div class="abs eq-item" style="top:692px"><span class="eq-icon"><svg width="16" height="18" viewBox="0 0 16 18"><path d="M8 1l6 2.5v5c0 4-3 7-6 8.5C5 15.5 2 12.5 2 8.5v-5z" fill="none" stroke="#fff" stroke-width="1.6"/><path d="M8 6v4" stroke="#fff" stroke-width="1.6"/></svg></span>Preventive Maintenance Programs</div>
  <div class="abs eq-item" style="top:733px"><span class="eq-icon"><svg width="18" height="18" viewBox="0 0 18 18"><path d="M4 14c0-5 2-9 5-10M9 4c3 1 5 4 5 8" fill="none" stroke="#fff" stroke-width="1.8" stroke-linecap="round"/><circle cx="13" cy="4" r="1.3" fill="#fff"/></svg></span>Equipment Cleaning &amp; Refurbishing</div>
  <div class="abs eq-item" style="top:770px"><span class="eq-icon"><svg width="16" height="18" viewBox="0 0 16 18"><circle cx="8" cy="7" r="5" fill="none" stroke="#fff" stroke-width="1.6"/><path d="M6 7l1.5 1.5L10.5 5.5" fill="none" stroke="#fff" stroke-width="1.4"/><path d="M5 11l-1 6 4-2 4 2-1-6" fill="none" stroke="#fff" stroke-width="1.4"/></svg></span>OEM Parts with 30-Day Warranty</div>
  <div class="abs eq-item" style="top:810px"><span class="eq-icon"><svg width="18" height="18" viewBox="0 0 18 18"><circle cx="8" cy="7" r="5" fill="none" stroke="#fff" stroke-width="1.6"/><path d="M8 4.5v5" stroke="#fff" stroke-width="1.4"/><path d="M2 16l4-3h5l4-2" fill="none" stroke="#fff" stroke-width="1.6" stroke-linecap="round"/></svg></span>Used Equipment Sales &amp; Rentals</div>

  <div class="abs badge badge-a" role="img" aria-label="Certified service technician badge"></div>
  <div class="abs badge badge-b" role="img" aria-label="Safety agency badge"></div>

  <div class="abs why">
    <div class="abs why-strip"></div>
    <div class="abs why-label">WHY CHOOSE US?</div>
    <ul class="abs why-list">
      <li><svg class="tick" viewBox="0 0 12 12"><circle cx="6" cy="6" r="6" fill="#ffd400"/><path d="M3.3 6.2l1.8 1.8 3.6-3.8" fill="none" stroke="#0b1f45" stroke-width="1.5"/></svg>CKTA Certified Technicians</li>
      <li><svg class="tick" viewBox="0 0 12 12"><circle cx="6" cy="6" r="6" fill="#ffd400"/><path d="M3.3 6.2l1.8 1.8 3.6-3.8" fill="none" stroke="#0b1f45" stroke-width="1.5"/></svg>OEM Parts for Maximum Reliability</li>
      <li><svg class="tick" viewBox="0 0 12 12"><circle cx="6" cy="6" r="6" fill="#ffd400"/><path d="M3.3 6.2l1.8 1.8 3.6-3.8" fill="none" stroke="#0b1f45" stroke-width="1.5"/></svg>Preventive Maintenance Subscribers Save on Labor Rates</li>
      <li><svg class="tick" viewBox="0 0 12 12"><circle cx="6" cy="6" r="6" fill="#ffd400"/><path d="M3.3 6.2l1.8 1.8 3.6-3.8" fill="none" stroke="#0b1f45" stroke-width="1.5"/></svg>Rapid Dispatch of Skilled Technicians</li>
      <li><svg class="tick" viewBox="0 0 12 12"><circle cx="6" cy="6" r="6" fill="#ffd400"/><path d="M3.3 6.2l1.8 1.8 3.6-3.8" fill="none" stroke="#0b1f45" stroke-width="1.5"/></svg>Local &amp; Trusted in the Denver Metro Area</li>
      <li><svg class="tick" viewBox="0 0 12 12"><circle cx="6" cy="6" r="6" fill="#ffd400"/><path d="M3.3 6.2l1.8 1.8 3.6-3.8" fill="none" stroke="#0b1f45" stroke-width="1.5"/></svg>Graffiti Removal Services Available</li>
    </ul>
  </div>

  <p class="abs emergency">EMERGENCY</p>
  <p class="abs repairs">REPAIRS</p>
  <svg class="abs" style="left:669px;top:844px" width="52" height="52" viewBox="0 0 52 52">
    <circle cx="25" cy="27" r="20" fill="#e8141b"/>
    <path d="M8 20a19 19 0 0 1 34-6" fill="none" stroke="#e8141b" stroke-width="3"/>
    <path d="M44 8l-1 8-7-2z" fill="#e8141b"/>
    <text x="25" y="31.5" text-anchor="middle" font-family="Poppins,sans-serif" font-weight="700" font-size="12.5" fill="#fff">24/7</text>
  </svg>
  <div class="abs avail">AVAILABILITY</div>

  <div class="abs footer"></div>
  <svg class="abs tab" viewBox="0 0 247 33" preserveAspectRatio="none"><path d="M0 0h247l-14 26q-4 7-12 7H26q-8 0-12-7z" fill="#ffd400"/></svg>
  <p class="abs tab-text">Full Facility Support</p>

  <ul class="abs support support-left">
    <li><svg class="tick" viewBox="0 0 12 12"><circle cx="6" cy="6" r="6" fill="#ffd400"/><path d="M3.3 6.2l1.8 1.8 3.6-3.8" fill="none" stroke="#0b1f45" stroke-width="1.5"/></svg>Painting, Drywall, Door Closers</li>
    <li><svg class="tick" viewBox="0 0 12 12"><circle cx="6" cy="6" r="6" fill="#ffd400"/><path d="M3.3 6.2l1.8 1.8 3.6-3.8" fill="none" stroke="#0b1f45" stroke-width="1.5"/></svg>Restaurant Furniture Repair/Replacement</li>
    <li><svg class="tick" viewBox="0 0 12 12"><circle cx="6" cy="6" r="6" fill="#ffd400"/><path d="M3.3 6.2l1.8 1.8 3.6-3.8" fill="none" stroke="#0b1f45" stroke-width="1.5"/></svg>Décor, Signage, Parking Lot &amp; Dumpster Area Repairs</li>
    <li><svg class="tick" viewBox="0 0 12 12"><circle cx="6" cy="6" r="6" fill="#ffd400"/><path d="M3.3 6.2l1.8 1.8 3.6-3.8" fill="none" stroke="#0b1f45" stroke-width="1.5"/></svg>Food Service Truck Equipment Repairs</li>
  </ul>
  <div class="abs divider"></div>
  <ul class="abs support support-right">
    <li><svg class="tick" viewBox="0 0 12 12"><circle cx="6" cy="6" r="6" fill="#ffd400"/><path d="M3.3 6.2l1.8 1.8 3.6-3.8" fill="none" stroke="#0b1f45" stroke-width="1.5"/></svg>&nbsp;OSHA Inspections</li>
    <li><svg class="tick" viewBox="0 0 12 12"><circle cx="6" cy="6" r="6" fill="#ffd400"/><path d="M3.3 6.2l1.8 1.8 3.6-3.8" fill="none" stroke="#0b1f45" stroke-width="1.5"/></svg>&nbsp;Handyman Services</li>
    <li><svg class="tick" viewBox="0 0 12 12"><circle cx="6" cy="6" r="6" fill="#ffd400"/><path d="M3.3 6.2l1.8 1.8 3.6-3.8" fill="none" stroke="#0b1f45" stroke-width="1.5"/></svg>&nbsp;Electrical Upgrades (Licensed Contractor)</li>
    <li><svg class="tick" viewBox="0 0 12 12"><circle cx="6" cy="6" r="6" fill="#ffd400"/><path d="M3.3 6.2l1.8 1.8 3.6-3.8" fill="none" stroke="#0b1f45" stroke-width="1.5"/></svg>&nbsp;Wall, Floor &amp; Ceiling Repairs</li>
  </ul>

  <div class="abs worker" role="img" aria-label="Smiling handyman in blue overalls and cap giving two thumbs up"></div>

  <div class="abs cta">Call Today for Fast, Professional Service</div>
  <div class="abs cta-note">We fix it all — if you have it, we probably fix it.</div>

  <div class="abs contacts">
    <span class="item"><svg width="14" height="14" viewBox="0 0 14 14"><path d="M3 1l2.3 2.8-1.3 1.6a8 8 0 0 0 4.6 4.6l1.6-1.3L13 11l-1.5 2C6 13 1 8 1 2.5z" fill="#ffd400"/></svg>555 0142 0199</span>
    <span class="sep">|</span>
    <span class="item"><svg width="16" height="12" viewBox="0 0 16 12"><rect x="0.5" y="0.5" width="15" height="11" rx="1" fill="#ffd400"/><path d="M1 1l7 5.5L15 1" fill="none" stroke="#0b1f45" stroke-width="1.2"/></svg>info@kitchenfixpro.com</span>
    <span class="sep">|</span>
    <span class="item"><svg width="15" height="15" viewBox="0 0 15 15"><circle cx="7.5" cy="7.5" r="6.5" fill="none" stroke="#ffd400" stroke-width="1.6"/><ellipse cx="7.5" cy="7.5" rx="2.8" ry="6.5" fill="none" stroke="#ffd400" stroke-width="1.3"/><path d="M1 7.5h13" stroke="#ffd400" stroke-width="1.3"/></svg>www.kitchenfixpro.com</span>
  </div>

</div>
</body>
</html>
```